Brightwave Reach - Business Card

We need a business card for a Social Media Marketing company that specializes in online marketing for small businesses in Canada using common Social Media platforms such as Pixlora, Chatterly, Blinkpost & Quibber.

I have uploaded a copy of our logo which I would like utilized in the business card. We would like the business card to be modern yet classy design.

Our website is www.brightwavereach.ca

Industry/Entity Type

Marketing

Contact Information for Business Card

Email: info@brightwavereach.ca
Website: www.brightwavereach.ca
Telephone: 604-555-0193

Colors

Designer to choose colors to be used in the design.

Requirements
Must have
• Social Media icons on reverse
• Please add some designs with color.

```html
<!DOCTYPE html>
<html lang="en">
<head>
<meta charset="utf-8">
<title>Brightwave Reach – Business Card</title>
<link rel="stylesheet" href="https://fonts.googleapis.com/css2?family=Roboto:wght@400;500;700&family=Roboto+Condensed:wght@500&display=swap">
<style>
  :root {
    --stage: #2a2b2c;
    --slate: #3c4043;
    --paper: #f1f1f0;
    --paper-edge: #fbfbfa;
    --ink-light: #ffffff;
    --ink-dark: #3c4043;
    --rule: #9ea1a3;
  }
  * { margin: 0; padding: 0; box-sizing: border-box; }
  html, body { width: 1200px; height: 960px; overflow: hidden; }
  body {
    background: var(--stage);
    position: relative;
    font-family: "Roboto", Arial, sans-serif;
  }
  .card { position: absolute; box-shadow: 0 4px 10px rgba(0,0,0,.45); }

  /* Front */
  .card-front {
    left: 314px; top: 113px; width: 600px; height: 342px;
    background: var(--paper-edge);
  }
  .front-panel {
    position: absolute; left: 15px; top: 12px; width: 279px; height: 318px;
    background: var(--slate); border-radius: 6px 0 0 6px;
  }
  .front-brand {
    position: absolute; left: 294px; top: 12px; width: 292px; height: 318px;
    background: var(--paper);
    border: 3px solid var(--slate); border-left: none;
    border-radius: 0 6px 6px 0;
    display: flex; align-items: center; justify-content: center;
  }
  .person-name {
    position: absolute; left: 48px; top: 98px;
    font-family: "Roboto Condensed", Arial, sans-serif;
    font-weight: 500; font-size: 21px; color: var(--ink-light);
  }
  .person-role {
    position: absolute; left: 48px; top: 125px;
    font-size: 14px; color: var(--ink-light);
  }
  .contact-list {
    position: absolute; left: 48px; top: 164px; list-style: none;
  }
  .contact-list li {
    display: flex; align-items: center; gap: 8px;
    font-size: 14px; color: var(--ink-light); height: 19.5px;
  }
  .contact-list svg { width: 13px; height: 13px; fill: var(--ink-light); }

  .brand-name {
    font-family: "Roboto", Arial, sans-serif;
    font-weight: 700; text-transform: uppercase;
    text-align: center; line-height: 1.05;
  }
  .front-brand .brand-name { font-size: 28px; color: var(--ink-dark); }

  /* Back */
  .card-back {
    left: 311px; top: 472px; width: 600px; height: 342px;
    background: var(--slate);
  }
  .card-back .brand-name {
    position: absolute; left: 0; right: 0; top: 118px;
    font-size: 34px; color: var(--ink-light);
  }
  .social-row {
    position: absolute; left: 0; right: 0; top: 285px;
    display: flex; align-items: center; justify-content: center; gap: 12px;
  }
  .social-rule { width: 110px; height: 1px; background: var(--rule); }
  .social-item {
    display: flex; align-items: center; gap: 5px;
    font-size: 12px; color: var(--ink-light);
  }
  .social-dot {
    width: 12px; height: 12px; border: 1.5px solid var(--ink-light); border-radius: 50%;
  }
</style>
</head>
<body>
  <section class="card card-front">
    <div class="front-panel">
      <h1 class="person-name">DANIEL REYES</h1>
      <p class="person-role">CEO/FOUNDER</p>
      <ul class="contact-list">
        <li>
          <svg viewBox="0 0 16 16" aria-hidden="true"><path d="M3.5 1l2.5 3-1.5 2c1 2 3 4 5 5l2-1.5 3 2.5-1.5 2.5C7 14 2 9 1 2.5z"/></svg>
          604-555-0193
        </li>
        <li>
          <svg viewBox="0 0 16 16" aria-hidden="true"><path d="M1 3h14v10H1z M1 3l7 5 7-5" fill="none" stroke="#fff" stroke-width="1.6"/></svg>
          info@brightwavereach.ca
        </li>
        <li>
          <svg viewBox="0 0 16 16" aria-hidden="true"><circle cx="8" cy="8" r="6.5" fill="none" stroke="#fff" stroke-width="1.6"/><path d="M1.5 8h13M8 1.5c-3 3-3 10 0 13M8 1.5c3 3 3 10 0 13" fill="none" stroke="#fff" stroke-width="1.2"/></svg>
          www.brightwavereach.ca
        </li>
      </ul>
    </div>
    <div class="front-brand">
      <p class="brand-name">Brightwave<br>Reach</p>
    </div>
  </section>

  <section class="card card-back">
    <p class="brand-name">Brightwave<br>Reach</p>
    <div class="social-row">
      <span class="social-rule"></span>
      <span class="social-item"><span class="social-dot"></span>Chatterly</span>
      <span class="social-item"><span class="social-dot"></span>Pixlora</span>
      <span class="social-item"><span class="social-dot"></span>Quibber</span>
      <span class="social-rule"></span>
    </div>
  </section>
</body>
</html>
```